Corporate Business Card

Very professional, Modern, Not to busy, include phone address email, website
(253) 617-4930, 18761 52nd Avenue S, Kent, WA 98047, martin@plumlinegroup.com, varkoworks.com

Target Market(s)

Manufacturing

Industry/Entity Type

Aero, machining, manufacturing, Off road racing

Contact Information for Business Card

Phone, address email, website

```html
<!DOCTYPE html>
<html lang="en">
<head>
<meta charset="utf-8">
<title>Varko Works — Business Card</title>
<link href="https://fonts.googleapis.com/css2?family=Titillium+Web:wght@400;700&display=swap" rel="stylesheet">
<style>
  :root {
    --navy: #17346e;
    --red: #d4212a;
    --white: #ffffff;
    --ink: #4a4a4f;
    --backdrop: #1f1f21;
  }
  * { margin: 0; padding: 0; box-sizing: border-box; }
  html, body {
    width: 1200px; height: 1122px; overflow: hidden;
    background: var(--backdrop);
    font-family: "Titillium Web", sans-serif;
  }
  .sheet {
    width: 1200px; height: 1122px;
    display: flex; flex-direction: column; align-items: center; justify-content: center;
    gap: 56px;
  }
  .card {
    width: 840px; height: 480px;
    border-radius: 28px;
    position: relative;
    overflow: hidden;
  }
  .card--back {
    background: var(--navy);
    display: flex; align-items: center; justify-content: center;
  }
  .card--front { background: var(--white); }

  .brand {
    display: flex; align-items: center; gap: 16px;
    font-weight: 700; text-transform: uppercase; letter-spacing: 2px;
    white-space: nowrap;
  }
  .brand__mark { width: 20px; height: 20px; background: var(--red); flex: none; }
  .card--back .brand { color: var(--white); font-size: 76px; gap: 18px; }
  .card--back .brand__mark { width: 30px; height: 30px; }
  .card--front .brand {
    position: absolute; left: 60px; top: 178px;
    color: var(--navy); font-size: 36px;
  }

  .divider {
    position: absolute; left: 440px; top: 112px;
    width: 3px; height: 256px;
    background: linear-gradient(to bottom, var(--navy) 0 18%, var(--red) 18% 100%);
  }

  .details { position: absolute; left: 478px; top: 112px; color: var(--ink); }
  .details__name {
    color: var(--red); font-weight: 700; font-size: 34px;
    text-transform: uppercase; line-height: 1.05; letter-spacing: 0.5px;
  }
  .details__title { color: var(--navy); font-size: 21px; line-height: 1.2; margin-bottom: 12px; }
  .details__address { font-size: 20px; line-height: 1.3; margin-bottom: 10px; }
  .contact { list-style: none; font-size: 20px; line-height: 1.45; }
  .contact li { display: flex; align-items: center; gap: 10px; }
  .contact svg { width: 16px; height: 16px; flex: none; fill: var(--navy); }
</style>
</head>
<body>
<main class="sheet">
  <section class="card card--back">
    <div class="brand"><span class="brand__mark"></span>Varko Works</div>
  </section>

  <section class="card card--front">
    <div class="brand"><span class="brand__mark"></span>Varko Works</div>
    <div class="divider"></div>
    <div class="details">
      <p class="details__name">Daniel Whitford</p>
      <p class="details__title">Managing Director</p>
      <p class="details__address">18761 52nd Avenue S<br>Kent, WA 98047</p>
      <ul class="contact">
        <li>
          <svg viewBox="0 0 24 24" aria-hidden="true"><path d="M6.6 10.8a15.1 15.1 0 0 0 6.6 6.6l2.2-2.2c.3-.3.7-.4 1-.2 1.1.4 2.3.6 3.6.6.6 0 1 .4 1 1V20c0 .6-.4 1-1 1A17 17 0 0 1 3 4c0-.6.4-1 1-1h3.5c.6 0 1 .4 1 1 0 1.3.2 2.5.6 3.6.1.3 0 .7-.2 1z"/></svg>
          (253) 617-4930
        </li>
        <li>
          <svg viewBox="0 0 24 24" aria-hidden="true"><path d="M2 5h20v14H2z M2 5l10 8 10-8" fill="none" stroke="#17346e" stroke-width="2"/></svg>
          martin@plumlinegroup.com
        </li>
        <li>
          <svg viewBox="0 0 24 24" aria-hidden="true"><circle cx="12" cy="12" r="9" fill="none" stroke="#17346e" stroke-width="2"/><path d="M3 12h18M12 3c3 3 3 15 0 18M12 3c-3 3-3 15 0 18" fill="none" stroke="#17346e" stroke-width="1.6"/></svg>
          www.varkoworks.com
        </li>
      </ul>
    </div>
  </section>
</main>
</body>
</html>
```